Website for Vornelix Capital, my new firm that raises money from investors to buy, build, own an...

Vornelix Capital needs a website! We are a new company with very experienced people, who invest in, own and build hotel properties, as well as apartments and other commercial real estate. We seek investors for our projects, and we provide safe, secure returns on their investment in our projects. Our new logo is designed to exhibit strength, class and security, and would like our website to continue on this theme. Our name, Vornelix, is a word-play on a Greek word “aristeia”, which means “excellence” and “a warriors finest moment of glory in war”. If you are in business, you realize that much of it is like war, with strategy and moves and opponents and competitors, and ever-changing economic conditions and threats that make business very much like war. We like to think that we are good at business (war), and so have named our company “Vornelix”, using the founders last name and the word “aristeia” combined. Another definition of "aristeia" is "performing at the peak of one's potential after a long struggle"...again, much like business in real life! The website design should exhibit financial security, smart moves, and positive growth towards a bright future.

Target Market(s)

The target market is smart and wealthy investors, with others such as brokers, cities and government agencies, lenders, sellers, partners, etc also looking at it.

Industry/Entity Type

Investment

Number of Pages Required

5+ page

Font styles to use
Sans Serif

Colors
fec214

Requirements
Must have
• Our website should have a landing page, a "about" or bio page, a projects page and a contact us page. Our new logo uses the colors black and gold, so this should be factored in to our site. The site should be simple, yet impactful and impressive. I have actually two logos, which can be mixed and interchanged in a complimentary way, each with their own unique look.
Nice to have
• I have uploaded a couple screenshots of a website i like, and the simplicity I mention.
Should not have
• The site should not be flashy or complicated or complex or "busy"

```html
<!DOCTYPE html>
<html lang="en">
<head>
<meta charset="utf-8">
<title>Vornelix Capital</title>
<link href="https://fonts.googleapis.com/css2?family=Roboto+Slab:wght@300;400;700&display=swap" rel="stylesheet">
<style>
:root{
  --gold:#c08a1e;
  --gold-band:#bf8b24;
  --black:#050505;
  --ink:#111111;
  --text:#333333;
  --light:#ececec;
  --white:#ffffff;
  --line:#d7d7d7;
}
*{margin:0;padding:0;box-sizing:border-box}
html,body{width:1200px;height:4455px;overflow:hidden}
body{font-family:"Roboto Slab",Georgia,serif;color:var(--text);background:var(--white);position:relative}
.abs{position:absolute}
.center{left:0;width:1200px;text-align:center}
.brand{font-weight:700;font-size:26px;letter-spacing:1px;color:var(--ink);display:flex;align-items:center;gap:10px;white-space:nowrap}
.brand-mark{width:18px;height:18px;background:var(--gold);flex:none}
/* header */
.site-header{top:0;left:0;width:1200px;height:128px;background:var(--white)}
.site-header .brand{position:absolute;left:163px;top:45px}
.nav{position:absolute;left:660px;top:42px;display:flex;border:2px solid var(--ink)}
.nav a{display:block;width:94px;height:44px;line-height:40px;text-align:center;font-size:14px;color:var(--ink);text-decoration:none;border-right:2px solid var(--ink)}
.nav a:last-child{border-right:none}
/* hero */
.hero{top:128px;left:0;width:1200px;height:579px;background:radial-gradient(ellipse at 50% 40%,#2c2c2a 0%,#141414 40%,#000 75%)}
.hero-title{top:318px;font-size:46px;font-weight:300;color:var(--white);letter-spacing:2px}
.hero-text{top:392px;font-size:21px;line-height:36px;font-weight:300;color:#dddddd}
.btn{display:inline-block;border:2px solid var(--gold);color:var(--gold);font-size:14px;text-transform:uppercase;text-align:center;background:transparent}
.hero-btn{left:517px;top:529px;width:166px;height:38px;line-height:34px}
.dots{top:634px;left:512px;display:flex;gap:8px}
.dots span{width:40px;height:4px;background:#777}
.dots span.on{background:var(--white)}
/* shared section */
.label{font-size:17px;font-weight:700;color:var(--gold);text-transform:uppercase}
.heading{font-size:47px;line-height:48px;color:var(--ink);font-weight:400}
.heading em{font-style:normal;color:var(--gold)}
.body-copy{font-size:21px;line-height:35px;color:var(--text);font-weight:300}
.welcome{top:707px;left:0;width:1200px;height:540px;background:var(--light)}
.outline-btn{width:166px;height:38px;line-height:34px;left:517px}
/* services */
.services{top:1247px;left:0;width:1200px;height:594px;background:var(--gold-band)}
.services-title{top:1310px;font-size:41px;color:var(--white);font-weight:400}
.services-sub{top:1375px;font-size:21px;color:#f4e3bf;font-weight:300}
.services-rule{top:1439px;left:555px;width:90px;height:3px;background:var(--white)}
.service{top:1491px;width:232px;text-align:center}
.service-icon{width:160px;height:160px;margin:0 auto;background:var(--white);border-radius:50%;display:flex;align-items:center;justify-content:center}
.service h3{margin-top:18px;font-size:19px;font-weight:400;line-height:24px;color:var(--white)}
.service p{margin:12px auto 0;width:160px;font-size:11px;line-height:16px;color:#f6ead0}
.divider-v{top:1491px;width:1px;height:290px;background:rgba(255,255,255,.25)}
/* projects */
.projects{top:1841px;left:0;width:1200px;height:686px;background:linear-gradient(180deg,#f8f4ee 0%,#f0e2cf 38%,#d9a98a 58%,#7c6a55 78%,#5d6a33 100%)}
.view-btn{left:517px;top:2210px;width:166px;height:38px;line-height:34px;border-color:var(--ink);color:var(--ink);background:rgba(255,255,255,.5)}
/* what we do */
.card{top:2804px;width:413px;height:404px;border:2px solid var(--line);border-radius:22px;background:var(--white);text-align:center}
.card svg{margin-top:40px}
.card h3{margin-top:18px;font-size:22px;font-weight:700;color:var(--gold)}
.card p{margin:20px auto 0;width:320px;font-size:20px;line-height:35px;color:var(--text);font-weight:300}
.card .btn{margin-top:26px;width:166px;height:38px;line-height:34px}
.amp{left:558px;top:2970px;width:84px;height:84px;border-radius:50%;border:2px solid var(--line);background:var(--white);color:var(--gold);font-size:32px;font-weight:700;text-align:center;line-height:78px}
/* quote */
.quote{top:3282px;left:0;width:1200px;height:490px;background:var(--black)}
.quote-text{top:3476px;font-size:24px;line-height:35px;font-style:italic;color:var(--white);font-weight:300}
.quote-name{top:3638px;font-size:18px;color:var(--gold)}
/* footer */
.footer{top:4321px;left:0;width:1200px;height:134px;background:var(--black)}
.footer .brand{position:absolute;left:163px;top:58px;color:var(--white);font-size:15px;letter-spacing:0;gap:6px}
.footer .brand-mark{width:12px;height:12px}
.foot-col{top:4355px;font-size:11px;line-height:22px;color:#e6e6e6;white-space:nowrap}
.foot-rule{left:823px;top:4350px;width:1px;height:84px;background:#444}
.socials{left:879px;top:4366px;display:flex;gap:8px}
.socials span{width:33px;height:33px;border:2px solid #cfcfcf;border-radius:50%}
.copyright{left:879px;top:4414px;font-size:10px;color:#bbbbbb;white-space:nowrap}
</style>
</head>
<body>

<header class="site-header abs">
  <div class="brand"><span class="brand-mark"></span>VORNELIX</div>
  <nav class="nav"><a href="#">HOME</a><a href="#">ABOUT</a><a href="#">PROJECTS</a><a href="#">CONTACT</a></nav>
</header>

<section class="hero abs" role="img" aria-label="Dark close-up photograph of coins and a plant"></section>
<h1 class="hero-title abs center">VORNELIX CAPITAL</h1>
<p class="hero-text abs center">Sed ut perspiciatis unde omnis iste natus error sit volu<br>tatem accusantium doloremque laudantium, totam rem<br>aperiam, eaque ipsa quae ab illo inventore verita</p>
<a class="btn hero-btn abs">Work with us</a>
<div class="dots abs"><span class="on"></span><span></span><span class="on"></span><span></span></div>

<section class="welcome abs"></section>
<p class="label abs center" style="top:789px">Welcome to Vornelix Capital</p>
<h2 class="heading abs center" style="top:834px">Sed ut perspiciatis unmnis<br>enatus error <em>sit voluptatem acc<br>usantium dolore</em> muelauum.</h2>
<p class="body-copy abs center" style="top:1004px">Sed ut perspiciatis unde omnis iste natus error sit volutatem<br>accusantium doloremque laudantium, totam rem aperia.</p>
<a class="btn outline-btn abs" style="top:1129px">Read more</a>

<section class="services abs"></section>
<h2 class="services-title abs center">Vornelix capital Services</h2>
<p class="services-sub abs center">Sed ut perspiciatis unde omnis iste natus error sit atem</p>
<div class="services-rule abs"></div>
<div class="divider-v abs" style="left:368px"></div>
<div class="divider-v abs" style="left:600px"></div>
<div class="divider-v abs" style="left:833px"></div>

<div class="service abs" style="left:136px">
  <div class="service-icon"><svg width="80" height="80" viewBox="0 0 80 80"><ellipse cx="36" cy="42" rx="26" ry="20" fill="none" stroke="#111" stroke-width="3"/><circle cx="56" cy="54" r="13" fill="#f28c1e" stroke="#111" stroke-width="2"/><text x="56" y="60" font-size="16" text-anchor="middle" fill="#111" font-family="Roboto Slab,serif">$</text></svg></div>
  <h3>Invest In</h3>
  <p>Sed ut perspiciatis unde omnis iste natus error sit voluptatem</p>
</div>
<div class="service abs" style="left:368px">
  <div class="service-icon"><svg width="80" height="80" viewBox="0 0 80 80"><path d="M12 62 L12 20 M12 62 L60 62" stroke="#111" stroke-width="3" fill="none"/><circle cx="46" cy="34" r="14" fill="#f28c1e" stroke="#111" stroke-width="2"/><text x="46" y="40" font-size="16" text-anchor="middle" fill="#111" font-family="Roboto Slab,serif">$</text></svg></div>
  <h3>Own and build<br>hotel properties</h3>
  <p>Sed ut perspiciatis unde omnis iste natus error sit voluptatem</p>
</div>
<div class="service abs" style="left:600px">
  <div class="service-icon"><svg width="80" height="80" viewBox="0 0 80 80"><rect x="18" y="26" width="44" height="40" fill="none" stroke="#111" stroke-width="3"/><rect x="14" y="18" width="52" height="8" fill="#f28c1e" stroke="#111" stroke-width="2"/><rect x="26" y="34" width="10" height="10" fill="#111"/><rect x="44" y="34" width="10" height="10" fill="#111"/><rect x="34" y="50" width="12" height="16" fill="#f28c1e"/></svg></div>
  <h3>Apartments</h3>
  <p>Sed ut perspiciatis unde omnis iste natus error sit voluptatem</p>
</div>
<div class="service abs" style="left:833px">
  <div class="service-icon"><svg width="80" height="80" viewBox="0 0 80 80"><path d="M14 62 L14 38 L40 20 L66 38 L66 62 Z" fill="none" stroke="#111" stroke-width="3"/><circle cx="40" cy="24" r="11" fill="#f28c1e" stroke="#111" stroke-width="2"/><text x="40" y="29" font-size="13" text-anchor="middle" fill="#111" font-family="Roboto Slab,serif">$</text></svg></div>
  <h3>Commercial<br>Real estate</h3>
  <p>Sed ut perspiciatis unde omnis iste natus error sit voluptatem</p>
</div>

<section class="projects abs" role="img" aria-label="Photograph of a couple looking at a new house in a field at sunset"></section>
<p class="label abs center" style="top:1935px">Our projects</p>
<h2 class="heading abs center" style="top:1981px">Sed ut perspiciatis unmnis<br>enatus error <em>sit voluptatem acc<br>usantium dolore</em> muelauum.</h2>
<p class="body-copy abs center" style="top:2139px">Sed ut perspiciatis unde omnis iste natus error sit atem</p>
<a class="btn view-btn abs">View projects</a>

<p class="label abs center" style="top:2607px">What we do</p>
<h2 class="heading abs center" style="top:2655px">Sed ut perspiciatis unmnis<br>enatus error <em>sit volupta</em></h2>

<div class="card abs" style="left:163px">
  <svg width="80" height="90" viewBox="0 0 80 90"><path d="M40 6 L72 18 L72 44 C72 66 56 80 40 86 C24 80 8 66 8 44 L8 18 Z" fill="none" stroke="#111" stroke-width="4"/><circle cx="40" cy="44" r="18" fill="#f2a61e" stroke="#111" stroke-width="3"/><text x="40" y="52" font-size="22" text-anchor="middle" fill="#111" font-family="Roboto Slab,serif">$</text></svg>
  <h3>We Provide Safe</h3>
  <p>Sed ut perspiciatis unde omnis iste natus error sit volutatem ac usantium doloremque lau.</p>
  <a class="btn">Read more</a>
</div>
<div class="amp abs">&amp;</div>
<div class="card abs" style="left:621px">
  <svg width="90" height="90" viewBox="0 0 90 90"><circle cx="36" cy="38" r="28" fill="none" stroke="#111" stroke-width="4"/><text x="36" y="48" font-size="28" text-anchor="middle" fill="#111" font-family="Roboto Slab,serif">$</text><rect x="52" y="58" width="28" height="24" rx="3" fill="#f2a61e" stroke="#111" stroke-width="3"/><path d="M58 58 L58 50 A8 8 0 0 1 74 50 L74 58" fill="none" stroke="#111" stroke-width="3"/></svg>
  <h3>Secure</h3>
  <p>Sed ut perspiciatis unde omnis iste natus error sit volutatem ac usantium doloremque lau.</p>
  <a class="btn">Read more</a>
</div>

<section class="quote abs"></section>
<svg class="abs" style="left:555px;top:3370px" width="90" height="60" viewBox="0 0 90 60"><path d="M4 30 A18 18 0 1 1 22 48 Q12 56 6 58 Q16 46 14 44 A18 18 0 0 1 4 30 Z" fill="#c08a1e"/><path d="M50 30 A18 18 0 1 1 68 48 Q58 56 52 58 Q62 46 60 44 A18 18 0 0 1 50 30 Z" fill="#c08a1e"/></svg>
<p class="quote-text abs center">" Sed ut perspiciatis unde omnis iste natus error sit volu<br>ptatem accusantium doloremque laudantium, totam rem<br>aperiam, eaque ipsa quae ab illo inventore veritatis et qu<br>asi architecto beatae vitae dicta sunt explica."</p>
<p class="quote-name abs center">Marek Dalton Reyes</p>

<p class="label abs center" style="top:3854px">Get started</p>
<h2 class="heading abs center" style="top:3911px">Sed ut perspiciatis unmnis<br>enatus error <em>sit voluptatem acc<br>usantium dolore</em> muelauum.</h2>
<p class="body-copy abs center" style="top:4081px">Sed ut perspiciatis unde omnis iste natus error sit volutatem<br>accusantium doloremque laudantium, totam rem aperia.</p>
<a class="btn outline-btn abs" style="top:4203px">Contact us</a>

<footer class="footer abs">
  <div class="brand"><span class="brand-mark"></span>VORNELIX</div>
</footer>
<div class="foot-col abs" style="left:288px">Lorem ipsum dolor<br>Sed dolorem ipsum<br>Eiusmod tempor</div>
<div class="foot-col abs" style="left:469px">Lorem ipsum dolor<br>Sed dolorem ipsum<br>Eiusmod tempor</div>
<div class="foot-col abs" style="left:656px">Lorem ipsum dolor<br>Sed dolorem ipsum<br>Eiusmod tempor</div>
<div class="foot-rule abs"></div>
<div class="socials abs"><span></span><span></span><span></span><span></span></div>
<p class="copyright abs">© 2016 All Rights Reserved.</p>

</body>
</html>
```